business card

Business card for new business.
Red and black corporate colors.
Card can have an Indsutrial feel to it. Feel free to add Rust, Bolted steel, or graphics as you see fit. We provide highly specialized services to the below mentioned industries.
Keep information out of corners so that if I want I can choose rounded corners.
Information
- front. name - title - phone - email
- Rear
Refining - Rail - Infrastructure - Mining - Energy
Calgary - Edmonton - Fort McMurray - Revelstoke - Vancouver

```html
<!DOCTYPE html>
<html lang="en">
<head>
<meta charset="utf-8">
<title>Girderline Business Card</title>
<link href="https://fonts.googleapis.com/css2?family=Lato:wght@400;700;900&display=swap" rel="stylesheet">
<style>
  :root {
    --bg: #3a3a3a;
    --card-black: #000000;
    --card-white: #ffffff;
    --brand-red: #e41e26;
    --steel-grey: #7a7a7a;
    --ink: #111111;
    --paper-text: #ffffff;
  }
  * { margin: 0; padding: 0; box-sizing: border-box; }
  html, body {
    width: 1200px; height: 1200px; overflow: hidden;
    background: var(--bg);
    font-family: 'Lato', sans-serif;
  }
  .sheet {
    position: relative; width: 1200px; height: 1200px;
    display: flex; flex-direction: column; align-items: center; justify-content: center; gap: 44px;
  }
  .card {
    position: relative; width: 900px; height: 514px; overflow: hidden;
    box-shadow: 0 12px 30px rgba(0,0,0,.45);
  }
  /* Rear */
  .card--rear { background: var(--card-black); color: var(--paper-text); }
  .card--rear .wordmark {
    position: absolute; top: 170px; left: 0; right: 0; text-align: center;
    font-size: 92px; font-weight: 900; letter-spacing: 2px; color: var(--steel-grey);
  }
  .services {
    position: absolute; left: 0; right: 0; bottom: 78px; text-align: center;
    font-size: 25px; line-height: 1.45; letter-spacing: .3px;
  }
  .services .dot { color: var(--brand-red); margin: 0 6px; }
  /* Front */
  .card--front { background: var(--card-white); color: var(--ink); }
  .card--front .wordmark {
    position: absolute; left: 70px; top: 222px; width: 370px;
    font-size: 56px; font-weight: 900; letter-spacing: 1px; color: var(--steel-grey);
    text-align: center;
  }
  .divider {
    position: absolute; left: 478px; top: 100px; width: 2px; height: 270px; background: var(--brand-red);
  }
  .details { position: absolute; left: 530px; top: 100px; }
  .person-name { font-size: 36px; font-weight: 700; color: var(--brand-red); line-height: 1.1; }
  .person-title { font-size: 24px; margin-top: 4px; }
  .address { font-size: 24px; line-height: 1.3; margin-top: 22px; }
  .contact { list-style: none; margin-top: 20px; font-size: 24px; line-height: 1.4; }
  .contact li { display: flex; align-items: center; gap: 16px; }
  .contact svg { width: 22px; height: 22px; flex: none; fill: var(--brand-red); }
  .base-band {
    position: absolute; left: 0; right: 0; bottom: 0; height: 18px; background: var(--brand-red);
  }
</style>
</head>
<body>
<main class="sheet">
  <section class="card card--rear" aria-label="Card rear">
    <div class="wordmark">GIRDERLINE</div>
    <p class="services">
      Petrochem<span class="dot">•</span>Transit<span class="dot">•</span>Civil Works<span class="dot">•</span>Quarrying<span class="dot">•</span>Power<br>
      Regina<span class="dot">•</span>Saskatoon<span class="dot">•</span>Prince George<span class="dot">•</span>Kamloops<span class="dot">•</span>Victoria
    </p>
  </section>

  <section class="card card--front" aria-label="Card front">
    <div class="wordmark">GIRDERLINE</div>
    <div class="divider"></div>
    <div class="details">
      <h1 class="person-name">Daniel Okafor</h1>
      <p class="person-title">Manager</p>
      <p class="address">418 Foundry Road<br>Houston, TX 77021</p>
      <ul class="contact">
        <li><svg viewBox="0 0 24 24" aria-hidden="true"><path d="M6.6 10.8a15.1 15.1 0 0 0 6.6 6.6l2.2-2.2c.3-.3.7-.4 1-.2 1.1.4 2.3.6 3.6.6.6 0 1 .4 1 1V20c0 .6-.4 1-1 1A17 17 0 0 1 3 4c0-.6.4-1 1-1h3.5c.6 0 1 .4 1 1 0 1.3.2 2.5.6 3.6.1.3 0 .7-.2 1z"/></svg>512 555 0147</li>
        <li><svg viewBox="0 0 24 24" aria-hidden="true"><path d="M2 5h20v2l-10 6L2 7zM2 9l10 6 10-6v10H2z"/></svg>info@girderline.com</li>
        <li><svg viewBox="0 0 24 24" aria-hidden="true"><path d="M12 2a10 10 0 1 0 0 20 10 10 0 0 0 0-20zm6.9 6h-3a15.6 15.6 0 0 0-1.3-3.8A8 8 0 0 1 18.9 8zM12 4c.8 1.2 1.5 2.5 1.9 4h-3.8c.4-1.5 1.1-2.8 1.9-4zM4.3 14a8 8 0 0 1 0-4h3.4a16.5 16.5 0 0 0 0 4zm.8 2h3a15.6 15.6 0 0 0 1.3 3.8A8 8 0 0 1 5.1 16zm3-8h-3a8 8 0 0 1 4.3-3.8C8.8 5.4 8.4 6.7 8.1 8zM12 20c-.8-1.2-1.5-2.5-1.9-4h3.8c-.4 1.5-1.1 2.8-1.9 4zm2.3-6H9.7a14.7 14.7 0 0 1 0-4h4.6a14.7 14.7 0 0 1 0 4zm.3 5.8c.6-1.2 1-2.5 1.3-3.8h3a8 8 0 0 1-4.3 3.8zm1.7-5.8a16.5 16.5 0 0 0 0-4h3.4a8 8 0 0 1 0 4z"/></svg>www.girderline.com</li>
      </ul>
    </div>
    <div class="base-band"></div>
  </section>
</main>
</body>
</html>
```